1876 Basins & Spouts Business Card

I'm wanting to get a business card designed. Our business is 1876 Basins & Spouts
Details for the card:

1876 Basins & Spouts
Name: Harold Vesk
Email: harold@1876basinsandspouts.com.au
Website: www.1876basinsandspouts.com.au
Mobile: 0438 260 947
Phone: 02 7481 3926

Font of Basins & Spouts is called Snell Roundhand. Not sue what font logo text is.

I'm thinking two sided but it doesn't have to be.

```html
<!DOCTYPE html>
<html lang="en">
<head>
<meta charset="utf-8">
<title>1876 Basins &amp; Spouts Business Card</title>
<link rel="stylesheet" href="https://fonts.googleapis.com/css2?family=Lato:wght@400;700&display=swap">
<style>
  :root {
    --page: #e9e9e9;
    --ink: #000000;
    --card-white: #ffffff;
    --card-black: #070707;
    --text-dark: #111111;
    --text-grey: #555555;
    --rule: #6a6a6a;
    --wave-grey: #8a8a8a;
    --on-dark: #ffffff;
  }
  * { margin: 0; padding: 0; box-sizing: border-box; }
  html, body {
    width: 1200px; height: 1200px; overflow: hidden;
    background: var(--page);
    font-family: "Lato", Arial, sans-serif;
  }
  .canvas { position: relative; width: 1200px; height: 1200px; }

  .card {
    position: absolute; left: 240px; width: 720px; height: 420px;
    border-radius: 30px; overflow: hidden;
  }
  .card--front { top: 142px; background: var(--card-white); }
  .card--back { top: 638px; background: var(--card-black); color: var(--on-dark); }

  .brand { position: absolute; display: flex; flex-direction: column; }
  .brand__row { display: flex; align-items: center; gap: 12px; }
  .brand__mark { width: 16px; height: 16px; border-radius: 50%; background: currentColor; }
  .brand__name { font-weight: 400; white-space: nowrap; }
  .brand__tagline { font-size: 10px; margin-top: 6px; white-space: nowrap; }

  .card--front .brand { left: 28px; top: 90px; color: var(--text-dark); }
  .card--front .brand__name { font-size: 26px; }
  .card--front .brand__tagline { margin-left: 28px; color: var(--text-grey); }

  .person {
    position: absolute; right: 30px; top: 170px;
    font-size: 25px; font-weight: 700; color: var(--text-dark);
  }
  .rule {
    position: absolute; left: 26px; right: 26px; top: 221px;
    height: 1px; background: var(--rule);
  }
  .contacts {
    position: absolute; right: 26px; top: 242px; list-style: none;
    display: flex; flex-direction: column; align-items: flex-end; gap: 7px;
  }
  .contacts__item {
    display: flex; align-items: center; gap: 10px;
    font-size: 17px; line-height: 19px; color: var(--text-grey);
  }
  .contacts__icon { width: 12px; height: 12px; fill: var(--text-dark); }

  .wave { position: absolute; left: 0; bottom: 0; width: 720px; height: 100px; }

  .card--back .brand { left: 50%; top: 187px; transform: translateX(-50%); align-items: center; }
  .card--back .brand__name { font-size: 36px; }
  .card--back .brand__tagline { font-size: 13px; margin-top: 8px; }
  .back-name {
    position: absolute; left: 0; right: 0; top: 358px;
    text-align: center; font-size: 17px;
  }
</style>
</head>
<body>
<main class="canvas">

  <section class="card card--front" aria-label="Card front">
    <div class="brand">
      <div class="brand__row">
        <span class="brand__mark"></span>
        <span class="brand__name">1876 Basins &amp; Spouts</span>
      </div>
      <span class="brand__tagline">Pairing enduring elegance with everyday usefulness</span>
    </div>

    <h1 class="person">Harold Vesk</h1>
    <div class="rule"></div>

    <ul class="contacts">
      <li class="contacts__item">02 7481 3926
        <svg class="contacts__icon" viewBox="0 0 12 12"><path d="M2 1l2 0 1 3-1.2 1a6 6 0 0 0 3.2 3.2L8 7l3 1v2a1 1 0 0 1-1 1A9 9 0 0 1 1 2a1 1 0 0 1 1-1z"/></svg>
      </li>
      <li class="contacts__item">0438 260 947
        <svg class="contacts__icon" viewBox="0 0 12 12"><path d="M3 0h6a1 1 0 0 1 1 1v10a1 1 0 0 1-1 1H3a1 1 0 0 1-1-1V1a1 1 0 0 1 1-1zm.5 1.5v7.5h5V1.5z"/></svg>
      </li>
      <li class="contacts__item">harold@1876basinsandspouts.com.au
        <svg class="contacts__icon" viewBox="0 0 12 12"><path d="M0 2h12v8H0zm1 1.2v.3l5 3.2 5-3.2v-.3z" fill-rule="evenodd"/></svg>
      </li>
      <li class="contacts__item">www.1876basinsandspouts.com.au
        <svg class="contacts__icon" viewBox="0 0 12 12"><circle cx="6" cy="6" r="6"/><path d="M3 3.5l2 .5 1 2-1.5 1.5.5 2.5-2-2zM7 2l2 1 .5 2-1.5-.5z" fill="#fff"/></svg>
      </li>
    </ul>

    <svg class="wave" viewBox="0 0 720 100" preserveAspectRatio="none" aria-hidden="true">
      <path d="M0 30 C 120 -5, 250 20, 400 40 C 540 58, 650 50, 720 16 L720 100 L0 100 Z" fill="var(--wave-grey)"/>
      <path d="M0 34 C 130 6, 260 26, 400 46 C 540 64, 650 56, 720 20 L720 100 L0 100 Z" fill="var(--card-white)"/>
      <path d="M0 36 C 130 10, 260 28, 400 50 C 540 70, 650 62, 720 22 L720 100 L0 100 Z" fill="var(--ink)"/>
      <path d="M0 44 C 140 18, 270 40, 410 60 C 550 78, 650 66, 720 30 L720 100 L0 100 Z" fill="var(--card-black)"/>
    </svg>
  </section>

  <section class="card card--back" aria-label="Card back">
    <div class="brand">
      <div class="brand__row">
        <span class="brand__mark"></span>
        <span class="brand__name">1876 Basins &amp; Spouts</span>
      </div>
      <span class="brand__tagline">Pairing enduring elegance with everyday usefulness</span>
    </div>
    <p class="back-name">1876 Basins &amp; Spouts</p>
  </section>

</main>
</body>
</html>
```